Business Card for Coastal Tundrabridge Advisory

We need a business card for Coastal Tundrabridge Advisory. The company website address is provided below. The company logo is attached. We provide specialized permafrost services to the mining, transportation, and oil & gas industries. The card should be prepared for:
Matthias Korhonen, PhD.
Coastal Tundrabridge Advisory
PO Box 418259
Quillwater, Alaska 99642
Direct: +1-907-555-0143
Email: mkorhonen@tundrabridgeadvisory.example
Website: www.coastaltundrabridgeadvisory.example

```html
<!DOCTYPE html>
<html lang="en">
<head>
<meta charset="utf-8">
<title>Coastal Tundrabridge Advisory – Business Card</title>
<link rel="stylesheet" href="https://fonts.googleapis.com/css2?family=Montserrat:wght@300;400;700&family=Open+Sans:wght@400;600&family=Roboto:wght@400;700&display=swap">
<style>
  :root {
    --stage: #232323;
    --card: #111826;
    --ink: #ffffff;
    --ink-soft: #e6e8ec;
    --deboss: #1a2231;
  }
  * { box-sizing: border-box; margin: 0; padding: 0; }
  html, body {
    width: 1200px; height: 711px; overflow: hidden;
    background: var(--stage);
  }
  .stage {
    position: relative; width: 1200px; height: 711px;
  }
  .card {
    position: absolute; top: 201px;
    width: 540px; height: 309px;
    background: var(--card);
    border-radius: 3px;
    overflow: hidden;
  }
  .card--back { left: 40px; }
  .card--front { left: 620px; }

  /* Back side */
  .back-name {
    position: absolute; left: 0; right: 0; top: 110px;
    text-align: center;
    font-family: "Montserrat", sans-serif; font-weight: 700;
    font-size: 25px; color: var(--deboss);
  }
  .services {
    position: absolute; left: 0; right: 0; bottom: 26px;
    text-align: center; color: var(--ink);
    font-family: "Roboto", sans-serif;
  }
  .services__title { font-weight: 700; font-size: 11px; margin-bottom: 3px; }
  .services__text { font-weight: 400; font-size: 10.5px; }

  /* Front side */
  .holder {
    position: absolute; left: 20px; bottom: 22px;
    writing-mode: vertical-rl; transform: rotate(180deg);
    color: var(--ink); font-family: "Montserrat", sans-serif;
  }
  .holder__name { font-size: 26px; line-height: 1.05; }
  .holder__first { font-weight: 700; }
  .holder__last { font-weight: 300; }
  .holder__title { font-size: 12px; font-weight: 400; margin-left: 2px; }

  .front-name {
    position: absolute; right: 26px; top: 32px;
    font-family: "Montserrat", sans-serif; font-weight: 700;
    font-size: 19px; color: var(--ink);
  }
  .address {
    position: absolute; right: 48px; top: 130px;
    text-align: right; color: var(--ink-soft);
    font-family: "Open Sans", sans-serif; font-size: 11.5px; line-height: 1.45;
  }
  .contacts {
    position: absolute; right: 22px; top: 184px;
    list-style: none; color: var(--ink-soft);
    font-family: "Open Sans", sans-serif; font-size: 11.5px;
  }
  .contacts li {
    display: flex; justify-content: flex-end; align-items: center;
    gap: 8px; line-height: 1; margin-bottom: 6px;
  }
  .contacts svg { width: 14px; height: 14px; flex: none; }
</style>
</head>
<body>
<main class="stage">
  <section class="card card--back" aria-label="Card back">
    <p class="back-name">Coastal Tundrabridge Advisory</p>
    <div class="services">
      <p class="services__title">OUR SERVICES</p>
      <p class="services__text">We provide specialized permafrost services to the mining, transportation, and oil &amp; gas industries</p>
    </div>
  </section>

  <section class="card card--front" aria-label="Card front">
    <div class="holder">
      <p class="holder__name"><span class="holder__first">Matthias</span> <span class="holder__last">Korhonen</span></p>
      <p class="holder__title">PhD</p>
    </div>

    <p class="front-name">Coastal Tundrabridge Advisory</p>

    <address class="address">PO Box 418259<br>Quillwater, Alaska 99642</address>

    <ul class="contacts">
      <li>+1-907-555-0143
        <svg viewBox="0 0 16 16" aria-hidden="true"><circle cx="8" cy="8" r="8" fill="#fff"/><path d="M5.2 4.2l1.6-.4.8 2-1 .8a5 5 0 0 0 2.8 2.8l.8-1 2 .8-.4 1.6c-3.8.2-6.8-2.8-6.6-6.6z" fill="#111826"/></svg>
      </li>
      <li>mkorhonen@tundrabridgeadvisory.example
        <svg viewBox="0 0 16 16" aria-hidden="true"><circle cx="8" cy="8" r="8" fill="#fff"/><rect x="3.8" y="5" width="8.4" height="6" fill="none" stroke="#111826" stroke-width="1.1"/><path d="M3.8 5L8 8.4 12.2 5" fill="none" stroke="#111826" stroke-width="1.1"/></svg>
      </li>
      <li>www.coastaltundrabridgeadvisory.example
        <svg viewBox="0 0 16 16" aria-hidden="true"><circle cx="8" cy="8" r="8" fill="#fff"/><circle cx="8" cy="8" r="4.5" fill="none" stroke="#111826" stroke-width="1"/><ellipse cx="8" cy="8" rx="2" ry="4.5" fill="none" stroke="#111826" stroke-width="1"/><path d="M3.5 8h9" stroke="#111826" stroke-width="1"/></svg>
      </li>
    </ul>
  </section>
</main>
</body>
</html>
```